Tallow Crest - Facebook Cover Photo & Photo Icon Design

We’re looking for a Facebook Cover Photo and Profile Icon design for Tallow Crest, a leading Residential Real Estate brand under Kestmore Property Agents, based in Capalaba and Alexandra Hills, Queensland, Australia.

This design will represent my professional real estate profile and needs to be bold, clean, and on-brand.

Deliverables:

Facebook Cover Photo (820 x 312 px, optimized for mobile + desktop)

Facebook Profile Icon (1:1 ratio, minimum 320 x 320 px)

Design Guidelines:

1. Must Include:

The Tallow Crest logo (provided after project start)

Use of the Kestmore Property Agents brand colour palette (will be supplied)

Clear connection to residential real estate

2. Optional but Preferred:

A local photo or skyline of Capalaba or Alexandra Hills in QLD (bonus points for this)

Space for a short tagline like:
“Selling Faster. Selling Smarter. Selling Kestmore.”
(Optional tagline – open to variations if it improves layout/design)

3. Style & Feel:

Professional yet personable

Clean, modern aesthetic

Subtle touches of fun or personality are welcome

Layout must work well when overlaid by Facebook UI elements (like profile photo & call-to-action buttons)

Who I Am:
I'm a well-known residential real estate agent in the Redlands area, known for high-energy campaigns, premium video marketing, and a results-driven approach. My brand is fun, fresh, and high-performing — just like the real estate campaigns I run.

Files to be Provided (after selection):

Tallow Crest logo in high-res

Brand colour palette / style reference

Optional photo references if local imagery is not sourced by designer

Final Notes:

Make sure all text is legible on mobile and desktop

Original, layered design files must be delivered (PSD or AI preferred)

Bonus points if it feels uniquely “Bayside Queensland” while maintaining a national-level professional polish

Target Market(s)

Alexandra Hills, Capalaba & Sheldon

Industry/Entity Type

Real Estate

Colors
0054AA
0677BA
7BADD7
CADEEF
E8F1F8

Requirements
Must have
• Headshot, Mobile Number 0417 962 085, Suburbs - Alexandra Hills, Capalaba & Sheldon
Nice to have
• White, Crisp & Professional. Bottom Banner with Suburb List. Specialising in Alexandra Hills, Capalaba & Sheldon

```html
<!DOCTYPE html>
<html lang="en">
<head>
<meta charset="utf-8">
<title>Tallow Crest – Facebook Cover &amp; Profile Icon</title>
<link href="https://fonts.googleapis.com/css2?family=Montserrat:wght@500;600&family=Saira+Semi+Condensed:wght@500;600&display=swap" rel="stylesheet">
<style>
  :root{
    --navy:#0c1a5e;
    --gold:#d6a865;
    --sky-top:#f4f6f8;
    --sky-mid:#e6ebee;
    --land:#d9ddd6;
    --suit:#3c4c63;
    --suit-deep:#2f3d55;
    --portrait-light:#cfd8e2;
    --page:#ecedef;
  }
  *{margin:0;padding:0;box-sizing:border-box}
  html,body{width:1200px;height:447px;overflow:hidden;background:var(--page)}
  .board{position:relative;width:1200px;height:447px}

  .artboard{position:absolute;overflow:hidden;background:var(--sky-top)}
  .cover{left:35px;top:43px;width:776px;height:295px}
  .profile{left:831px;top:35px;width:302px;height:303px}

  .scenery{position:absolute;inset:0;
    background:linear-gradient(180deg,var(--sky-top) 0%,var(--sky-mid) 35%,var(--land) 100%);opacity:.9}
  .profile .scenery{background:linear-gradient(180deg,#f2f5f8 0%,#dfe7ee 50%,#c9d6e0 100%)}

  .brand-name{position:absolute;font-family:"Montserrat",Arial,sans-serif;font-weight:500;
    color:var(--navy);letter-spacing:.06em;line-height:1;text-transform:uppercase}
  .cover .brand-name{left:30px;top:28px;font-size:44px}
  .profile .brand-name{left:13px;top:14px;font-size:31px}

  .tagline{position:absolute;font-family:"Saira Semi Condensed","Arial Narrow",sans-serif;font-weight:500;
    color:var(--navy);line-height:1.22;white-space:nowrap}
  .cover .tagline{left:30px;top:132px;font-size:30px}
  .profile .tagline{left:13px;top:87px;font-size:21px;line-height:1.25}

  .bar{position:absolute;left:0;right:0;bottom:0;background:var(--navy)}
  .cover .bar{height:74px}
  .profile .bar{height:83px}

  .agent{position:absolute;font-family:"Montserrat",Arial,sans-serif;font-weight:500;
    color:var(--gold);line-height:1.65;white-space:nowrap}
  .cover .agent{left:30px;top:247px;font-size:16px}
  .profile .agent{left:13px;top:249px;font-size:15px}

  .phone{position:absolute;display:flex;align-items:center;white-space:nowrap;
    font-family:"Saira Semi Condensed","Arial Narrow",sans-serif;font-weight:600;line-height:1}
  .phone svg{display:block;flex:none}
  .cover .phone{left:303px;top:255px;font-size:29px;color:var(--gold);gap:11px}
  .profile .phone{left:13px;top:184px;font-size:22px;color:var(--navy);gap:8px}

  .headshot{position:absolute;
    background:linear-gradient(180deg,var(--portrait-light) 0%,#8795a8 30%,var(--suit) 60%,var(--suit-deep) 100%);
    border-radius:48% 48% 0 0 / 30% 30% 0 0}
  .cover .headshot{left:560px;top:28px;width:216px;height:267px}
  .profile .headshot{left:196px;top:142px;width:106px;height:161px}
</style>
</head>
<body>
<main class="board">

  <section class="artboard cover" aria-label="Facebook cover photo, 820 by 312">
    <div class="scenery" role="img" aria-label="Faded aerial view of bayside suburbs"></div>
    <div class="brand-name">Tallow<br>Crest</div>
    <p class="tagline">Selling Faster. Selling Smarter.<br>Selling Kestmore.</p>
    <div class="bar"></div>
    <p class="agent">Rowan Adler<br>Suburb Specialist</p>
    <p class="phone">
      <svg width="32" height="32" viewBox="0 0 24 24" fill="none" stroke="currentColor" stroke-width="1.4" stroke-linecap="round" stroke-linejoin="round" aria-hidden="true">
        <path d="M6.5 3.5 9 3l1.6 4-2 1.4a11 11 0 0 0 7 7l1.4-2 4 1.6-.5 2.5a2 2 0 0 1-2 1.6A16 16 0 0 1 3 4.9a2 2 0 0 1 1.6-1.9z"/>
        <path d="M14 3.5a6.5 6.5 0 0 1 6.5 6.5M14 6.5a3.5 3.5 0 0 1 3.5 3.5"/>
      </svg>
      0417 962 085
    </p>
    <div class="headshot" role="img" aria-label="Headshot of the agent in a navy blazer"></div>
  </section>

  <section class="artboard profile" aria-label="Facebook profile icon, 320 by 320">
    <div class="scenery" role="img" aria-label="Faded coastal skyline"></div>
    <div class="brand-name">Tallow<br>Crest</div>
    <p class="tagline">Selling Faster. Selling Smarter.<br>Selling Kestmore.</p>
    <p class="phone">
      <svg width="25" height="25" viewBox="0 0 24 24" fill="none" stroke="currentColor" stroke-width="1.5" stroke-linecap="round" stroke-linejoin="round" aria-hidden="true">
        <path d="M6.5 3.5 9 3l1.6 4-2 1.4a11 11 0 0 0 7 7l1.4-2 4 1.6-.5 2.5a2 2 0 0 1-2 1.6A16 16 0 0 1 3 4.9a2 2 0 0 1 1.6-1.9z"/>
        <path d="M14 3.5a6.5 6.5 0 0 1 6.5 6.5M14 6.5a3.5 3.5 0 0 1 3.5 3.5"/>
      </svg>
      0417 962 085
    </p>
    <div class="bar"></div>
    <p class="agent">Rowan Adler<br>Suburb Specialist</p>
    <div class="headshot" role="img" aria-label="Headshot of the agent in a navy blazer"></div>
  </section>

</main>
</body>
</html>
```